Online Shop - Website Design for up an coming art studio

We require a fully functional website design - not just design - but complete coded online shop website please, which should be a word press style frame work to allow ease up updating the site in the future. The website will sell art work from up and coming artists. The business is called "Brindle Harbor Studios". I have attached our logo to allow the submitted designs to tie in with this.

Industry/Entity Type

Shop

Coding

Coded - Design and coding required

Number of Pages Required

1 page

Colors

Designer to choose colors to be used in the design.

Requirements
Must have
• The website design must incorporate and fully functional online eCommerce shop feature.

```html
<!DOCTYPE html>
<html lang="en">
<head>
<meta charset="utf-8">
<title>Brindle Harbor Studios</title>
<link rel="stylesheet" href="https://fonts.googleapis.com/css2?family=Rubik:wght@400;500;700&family=Open+Sans:ital,wght@0,400;0,600;1,400&display=swap">
<style>
:root{
  --ink:#333336;
  --grey-line:#a9aaad;
  --nav:#a7a8ab;
  --red:#e5173f;
  --orange:#f7941d;
  --blue:#29abe2;
  --green:#8cc63f;
  --magenta:#e6178a;
  --footer:#3c3c3f;
  --footer-bar:#303033;
  --white:#ffffff;
}
*{margin:0;padding:0;box-sizing:border-box}
html,body{width:924px;height:1200px;overflow:hidden;background:var(--white)}
body{position:relative;font-family:"Rubik",sans-serif;color:var(--ink)}
.abs{position:absolute}

/* header */
.top-rule{left:0;top:0;width:924px;height:3px;background:var(--grey-line)}
.cart{left:116px;top:56px;display:flex;align-items:center;gap:8px;font-size:10.5px}
.brand{left:312px;top:10px;width:300px;text-align:center}
.brand-mark{width:78px;height:78px;margin:0 auto;border-radius:50%;background:#3a3a3d}
.brand-name{margin-top:14px;font-size:19px;font-weight:500;letter-spacing:2px;color:#4a4a4d}
.address{font-size:10px;line-height:16px;text-align:right}
.header-address{left:630px;top:38px;width:184px}
.pin{position:absolute}

/* nav */
.nav{left:0;top:134px;width:924px;height:41px;background:var(--nav)}
.nav a{position:absolute;top:13px;font-size:12.5px;font-weight:500;color:var(--white);text-decoration:none;letter-spacing:.4px}
.nav-strip{left:101px;width:45px;height:3px;background:linear-gradient(90deg,#e5173f 0 20%,#f7941d 20% 40%,#8cc63f 40% 60%,#29abe2 60% 80%,#e6178a 80%)}
.social{top:141px;width:27px;height:27px;border-radius:50%;background:#3a3a3d;border:2px dashed #222}
.social i{position:absolute;inset:4px;border-radius:50%}

/* hero */
.hero{left:0;top:175px;width:924px;height:391px;background:radial-gradient(ellipse at 70% 45%,#fdf3d6 0%,#f4ead2 30%,#dfe2f0 65%,#cdd3ea 100%)}
.frame{background:#3f3f42;padding:8px}
.frame div{width:100%;height:100%}
.hero-title{left:497px;top:300px;font-size:28px;font-weight:700;white-space:nowrap}
.hero-title .t1{color:#a7a8ab}.hero-title .t2{color:var(--ink)}.hero-title .t3{color:var(--red)}
.hero-text{left:497px;top:338px;width:330px;font-size:10.5px;line-height:16px}
.btn{display:flex;align-items:center;justify-content:center;color:var(--white);font-weight:500;font-size:10.5px;letter-spacing:.4px}
.btn-learn{left:497px;top:383px;width:97px;height:25px;background:var(--orange)}
.btn-buy{left:601px;top:383px;width:83px;height:25px;background:var(--blue)}

/* releases */
.section-title{left:93px;top:602px;font-size:20.5px;font-weight:700;color:var(--red)}
.section-text{left:93px;top:639px;width:254px;font-family:"Open Sans",sans-serif;font-size:9.6px;line-height:16px;text-align:justify}
.btn-read{left:93px;top:750px;width:79px;height:25px;background:var(--green);font-family:"Open Sans",sans-serif;font-size:11px;font-weight:600;border-radius:2px}
.card{background:var(--white);box-shadow:0 2px 6px rgba(0,0,0,.22);padding:6px}
.card .art{width:100%;height:100%;border:3px solid #111}
.nav-arrow{top:687px;width:28px;height:52px;background:rgba(40,40,40,.75);display:flex;align-items:center;justify-content:center}
.caption{left:517px;top:764px;width:171px;height:52px;background:var(--white);padding:6px 10px}
.caption h4{font-size:11px;font-weight:500;color:#555}
.caption p{font-family:"Open Sans",sans-serif;font-style:italic;font-size:7px;line-height:9px;color:#777;width:115px;margin-top:3px}
.caption .price{position:absolute;right:10px;top:18px;font-size:13px;font-weight:500;color:#555}
.cart-badge{left:579px;top:679px;width:37px;height:33px;background:var(--magenta);display:flex;align-items:center;justify-content:center}
.btn-gallery{left:544px;top:841px;width:117px;height:26px;background:var(--magenta);font-size:11px;border-radius:1px}

/* footer */
.footer-shape{left:0;top:894px}
.footer-logo{left:443px;top:906px;width:38px;height:38px;border-radius:50%;background:#d8d8d8;border:3px solid #f0f0f0}
.footer-name{left:312px;top:956px;width:300px;text-align:center;font-size:11px;color:#d9d9d9;letter-spacing:1.5px}
.footer-title{left:312px;top:995px;width:300px;text-align:center;font-size:13px;color:var(--white);letter-spacing:.8px}
.footer-address{left:150px;top:1042px;width:180px;color:var(--white)}
.map{left:375px;top:1030px;width:362px;height:118px;background:linear-gradient(135deg,#ecebe6,#e2e0da)}
.footer-bar{left:0;top:1165px;width:924px;height:35px;background:var(--footer-bar);font-family:"Open Sans",sans-serif;font-size:9px;color:#e6e6e6}
.footer-bar a{position:absolute;top:12px;color:#e6e6e6;text-decoration:none}
.footer-bar .copy{position:absolute;top:12px;left:585px;font-size:8.4px}
</style>
</head>
<body>

<div class="abs top-rule"></div>

<header>
  <div class="abs cart">
    <svg width="14" height="14" viewBox="0 0 14 14" fill="none" stroke="#333" stroke-width="1.2"><path d="M1 2h2l2 7h7l1.5-5H4"/><circle cx="6" cy="12" r="1"/><circle cx="11" cy="12" r="1"/></svg>
    <span>Shopping Cart : item(0)</span>
  </div>
  <div class="abs brand">
    <div class="brand-mark"></div>
    <div class="brand-name">BRINDLE HARBOR</div>
  </div>
  <div class="abs address header-address">42 Larkspur Lane,<br>Millbrook, Eastshire,<br>Northland, EB4 7KQ</div>
  <svg class="pin" style="left:822px;top:41px" width="14" height="17" viewBox="0 0 14 17" fill="none" stroke="#333" stroke-width="1.2"><path d="M7 16s6-6 6-9.5A6 6 0 0 0 1 6.5C1 10 7 16 7 16z"/><circle cx="7" cy="6.5" r="2"/></svg>
</header>

<div class="abs nav-strip" style="top:130px"></div>
<nav class="abs nav">
  <a style="left:108px">HOME</a>
  <a style="left:172px">ABOUT US</a>
  <a style="left:262px">ARTISTS</a>
  <a style="left:342px">BLOG</a>
  <a style="left:403px">CONTACT US</a>
</nav>
<div class="abs nav-strip" style="top:175px"></div>
<div class="abs social" style="left:745px"><i style="background:#3fa9e0"></i></div>
<div class="abs social" style="left:778px"><i style="background:#3b5bab"></i></div>
<div class="abs social" style="left:811px"><i style="background:#555"></i></div>

<section class="abs hero">
  <div class="abs frame" style="left:130px;top:38px;width:229px;height:295px">
    <div role="img" aria-label="Painting of a couple with a red umbrella on a snowy city street" style="background:linear-gradient(160deg,#e9ecef,#b7bcc2 55%,#c9595a 80%,#dfe3e6)"></div>
  </div>
  <div class="abs frame" style="left:266px;top:130px;width:185px;height:232px;transform:rotate(7deg)">
    <div role="img" aria-label="Photo of an artist painting at an easel in a studio" style="background:linear-gradient(150deg,#e6ded0,#a08b70 55%,#5a5048)"></div>
  </div>
</section>
<h1 class="abs hero-title"><span class="t1">Brindle</span> <span class="t2">Harbor</span> <span class="t3">Studios</span></h1>
<p class="abs hero-text">Lorem ipsum dolor sit amet, consectetur adipiscing elit, sed do eiusmod tempor incididunt ut labore et...</p>
<div class="abs btn btn-learn">LEARN MORE</div>
<div class="abs btn btn-buy">BUY NOW</div>
<svg class="abs" style="left:502px;top:449px" width="32" height="18" viewBox="0 0 32 18" fill="none" stroke="#666" stroke-width="1.3"><path d="M8 1L1 9l7 8M24 1l7 8-7 8"/></svg>

<section>
  <h2 class="abs section-title">New Releases</h2>
  <p class="abs section-text">Nam libero tempore, cum soluta nobis est eligendi optio cumque nihil impedit quo minus id quod maxime placeat facere possimus, omnis voluptas assumenda est, omnis dolor repellendus. Temporibus autem quibusdam et aut officiis debitis aut rerum necessitatibus saepe eveniet ut et voluptates repudiandae</p>
  <div class="abs btn btn-read">Read more</div>

  <div class="abs card" style="left:381px;top:622px;width:128px;height:189px">
    <div class="art" role="img" aria-label="Faded painting of a riverside village with a boat" style="background:linear-gradient(160deg,#e8e1d4,#c9c2aa 50%,#a8ab98)"></div>
  </div>
  <div class="abs card" style="left:698px;top:622px;width:135px;height:189px">
    <div class="art" role="img" aria-label="Colourful painted portrait artwork" style="background:linear-gradient(150deg,#c9a98a,#4b6e8f 50%,#b58a6a)"></div>
  </div>
  <div class="abs card" style="left:505px;top:596px;width:195px;height:233px">
    <div class="art" role="img" aria-label="Sepia painting of a stone temple statue" style="background:linear-gradient(160deg,#d9c9a0,#8d7a55 55%,#5c5140)"></div>
  </div>
  <div class="abs cart-badge">
    <svg width="16" height="14" viewBox="0 0 14 14" fill="none" stroke="#fff" stroke-width="1.2"><path d="M1 2h2l2 7h7l1.5-5H4"/><circle cx="6" cy="12" r="1"/><circle cx="11" cy="12" r="1"/></svg>
  </div>
  <div class="abs caption">
    <h4>Lorium ipsum</h4>
    <p>Nor again is there anyone who loves or pursues or desires</p>
    <span class="price">$50</span>
  </div>
  <div class="abs nav-arrow" style="left:392px">
    <svg width="10" height="14" viewBox="0 0 10 14" fill="none" stroke="#fff" stroke-width="2.2"><path d="M8 1L2 7l6 6"/></svg>
  </div>
  <div class="abs nav-arrow" style="left:794px">
    <svg width="10" height="14" viewBox="0 0 10 14" fill="none" stroke="#fff" stroke-width="2.2"><path d="M2 1l6 6-6 6"/></svg>
  </div>
  <div class="abs btn btn-gallery">View Our Gallery</div>
</section>

<footer>
  <svg class="abs footer-shape" width="924" height="271" viewBox="0 0 924 271"><polygon points="0,39 232,39 462,0 693,39 924,39 924,271 0,271" fill="#3c3c3f"/></svg>
  <div class="abs footer-logo"></div>
  <div class="abs footer-name">BRINDLE HARBOR</div>
  <div class="abs footer-title">CONTACT US</div>
  <div class="abs address footer-address">42 Larkspur Lane,<br>Millbrook, Eastshire,<br>Northland, EB4 7KQ</div>
  <svg class="pin" style="left:338px;top:1044px" width="14" height="17" viewBox="0 0 14 17" fill="none" stroke="#fff" stroke-width="1.2"><path d="M7 16s6-6 6-9.5A6 6 0 0 0 1 6.5C1 10 7 16 7 16z"/><circle cx="7" cy="6.5" r="2"/></svg>
  <div class="abs map" role="img" aria-label="Street map showing the studio location"></div>
  <div class="abs footer-bar">
    <a style="left:80px">Home</a>
    <a style="left:128px">About Us</a>
    <a style="left:189px">Artists</a>
    <a style="left:238px">Blog</a>
    <a style="left:278px">Contact Us</a>
    <span class="copy">Copyright © 2017 www.brindleharbor.com &nbsp;| &nbsp;All Rights Reserved.</span>
  </div>
</footer>

</body>
</html>
```